We need a complete design for our construction company KELTO CONSTRUCTION based in Auckland New Zealand, we need a logo, website, business card, vehicle design etc..
We are a mid to high-end construction company who work mostly on residential projects and some commercial.

What we want to see in the design;
Professional,
Architectural,
Simple,
Alternative,

We want the design to communicate professionalism, high quality wormanship and and quality service.

Target Market(s)

People looking for a quality building/ construction company

Industry/Entity Type

Construction Company

Contact Information for Business Card

KELTO CONSTRUCTION.co.nz
Lino Verasek
lino@keltoconstruction.example.nz
021 5807 462

Logo Text

KELTO CONSTRUCTION

Number of Pages Required

5+ page

Font styles to use
Sans Serif

Colors

Designer to choose colors to be used in the design.

Requirements
Must have
• Must appear high end, professional, quality, be simple, easy to use, give security to potential clients
Nice to have
• high-quality photos of our recent projects
• about us page
• blog page
• contact us page
• high quality content
Should not have
• should not be hard to use and have too much going on.

```html
<!DOCTYPE html>
<html lang="en">
<head>
<meta charset="utf-8">
<title>KELTO CONSTRUCTION</title>
<link rel="stylesheet" href="https://fonts.googleapis.com/css2?family=Lato:wght@400;700;900&family=Michroma&family=Oswald:wght@400;500&display=swap">
<style>
:root{
  --navy:#0d4b7a;
  --navy-dark:#0a3d64;
  --grey-band:#8b8c8e;
  --btn:#7c7e81;
  --text:#333;
  --muted:#555;
  --soft:#efefef;
  --footer:#323232;
  --white:#fff;
  --heading-grey:#6d6f72;
}
*{box-sizing:border-box;margin:0;padding:0}
html,body{width:1200px;height:3255px;overflow:hidden}
body{font-family:"Lato",sans-serif;color:var(--text);background:var(--white);position:relative}
.abs{position:absolute}
.display{font-family:"Michroma",sans-serif;-webkit-text-stroke:.5px currentColor}
.heading{font-family:"Michroma",sans-serif;font-size:22px;text-align:center;letter-spacing:.5px;color:var(--navy);-webkit-text-stroke:.7px currentColor}
.heading span{color:var(--heading-grey)}
.divider{display:flex;align-items:center;justify-content:center;gap:10px;margin-top:16px}
.divider i{display:block;width:50px;height:1px;background:#aaa}
.divider b{display:block;width:18px;height:18px;border-radius:50%;background:var(--navy)}
.btn{display:inline-block;background:var(--btn);color:var(--white);font:900 12px "Lato",sans-serif;letter-spacing:.5px;padding:10px 18px;text-transform:uppercase}

/* header */
.header{top:0;left:0;width:1200px;height:128px;background:var(--white)}
.brand{left:98px;top:26px;display:flex;align-items:center;gap:12px}
.brand-mark{width:46px;height:46px;background:var(--navy);flex:none}
.brand-name{font-family:"Michroma",sans-serif;font-size:17px;color:var(--navy);line-height:1.3;letter-spacing:.5px}
.topbar{right:100px;top:20px;display:flex;align-items:center;gap:18px;font-size:14px;color:#555}
.topbar .ico{width:30px;height:30px;border-radius:50%;background:var(--navy-dark);display:inline-flex;align-items:center;justify-content:center;margin-right:8px;vertical-align:middle}
.socials{display:flex;gap:6px}
.socials span{width:32px;height:32px;border-radius:50%;display:block}
.nav{right:104px;top:82px;display:flex;gap:40px;font:700 15px "Lato",sans-serif;color:#555;letter-spacing:.8px}
.nav .active{color:var(--navy);border-bottom:2px solid var(--navy);padding-bottom:4px}

/* hero */
.hero{top:128px;left:0;width:1200px;height:512px;background:linear-gradient(180deg,#d7d3c6 0%,#c8c6bb 18%,#9fb0be 38%,#6b7886 52%,#434d58 62%,#56708a 70%,#6f8aa2 84%,#8aa0b3 100%)}
.hero-title{position:absolute;left:0;right:0;top:355px;text-align:center;color:var(--white);font-family:"Oswald",sans-serif;text-shadow:0 2px 6px rgba(0,0,0,.55)}
.hero-title .l1{font-size:42px;line-height:1.15}
.hero-title .l2{font-size:58px;line-height:1.1;font-weight:500}
.arrow{top:215px;width:36px;height:36px;background:rgba(20,20,20,.75);display:flex;align-items:center;justify-content:center}

/* project bands */
.band{top:640px;height:135px;width:600px;display:flex;align-items:center;padding-left:98px;gap:30px;color:var(--white)}
.band.resi{left:0;background:var(--grey-band)}
.band.comm{left:600px;background:var(--navy);padding-left:42px}
.band .circle{width:104px;height:104px;border-radius:50%;flex:none;display:flex;align-items:center;justify-content:center}
.band.resi .circle{background:var(--navy)}
.band.comm .circle{background:#8a8b8d}
.band h3{font-family:"Michroma",sans-serif;font-size:13.5px;font-weight:400;letter-spacing:.5px;margin-bottom:8px;-webkit-text-stroke:.4px currentColor}
.band p{font-size:13px;line-height:1.45;width:350px}

/* about */
.about{top:775px;left:0;width:1200px;height:330px;text-align:center}
.about .heading{margin-top:48px}
.about p{width:1090px;margin:24px auto 20px;font-size:13px;line-height:2;color:var(--muted)}

/* specialties */
.special{top:1105px;left:0;width:1200px;height:615px;background:var(--soft)}
.special .heading{margin-top:53px}
.card{top:147px;width:316px;height:413px;background:var(--white);border:1px solid #ddd;border-bottom:3px solid var(--navy);text-align:center}
.card .photo{margin:4px;height:186px}
.card .badge{width:72px;height:72px;border-radius:50%;background:var(--navy);border:4px solid var(--white);margin:-40px auto 0;position:relative;display:flex;align-items:center;justify-content:center}
.card h4{font-family:"Michroma",sans-serif;font-weight:400;font-size:13.5px;letter-spacing:.3px;margin:16px 0 10px;color:#222;-webkit-text-stroke:.4px currentColor}
.card p{font-size:13px;line-height:1.55;color:#444;padding:0 38px;margin-bottom:14px}

/* work */
.work{top:1720px;left:0;width:1200px;height:630px}
.work .heading{margin-top:48px}
.tile{display:flex;align-items:flex-end;justify-content:center;overflow:hidden}
.tile .cap{width:100%;background:rgba(90,90,90,.72);color:var(--white);text-align:center;font:900 12px "Lato",sans-serif;padding:9px 0;letter-spacing:.5px}
.work .btn,.blog .btn{position:absolute;left:50%;transform:translateX(-50%)}

/* blog */
.blog{top:2350px;left:0;width:1200px;height:565px;background:var(--soft)}
.blog .heading{margin-top:53px}
.feature{left:98px;top:137px;width:487px;height:310px;background:linear-gradient(160deg,#c9dbea 0%,#7fa5c8 28%,#3f6e9e 52%,#27507c 72%,#8c8f8e 100%)}
.feature .meta{position:absolute;left:22px;bottom:14px;color:var(--white)}
.feature .meta h5{font:700 15px "Lato",sans-serif;margin-bottom:4px}
.meta-row{display:flex;gap:26px;font-size:12px;align-items:center}
.meta-row span{display:flex;align-items:center;gap:5px}
.post{left:617px;width:483px;height:95px;display:flex;gap:15px}
.post .thumb{width:113px;height:95px;flex:none}
.post h5{font:900 15px "Lato",sans-serif;color:#222;margin:2px 0 5px}
.post .meta-row{color:#444;gap:40px;margin-bottom:6px}
.post p{font-size:12px;line-height:1.5;color:#444}

/* footer */
.footer{top:2915px;left:0;width:1200px;height:295px;background:var(--footer);color:#e8e8e8}
.footer h6{font-family:"Michroma",sans-serif;font-weight:400;font-size:12px;letter-spacing:.5px;color:var(--white);margin-bottom:28px;-webkit-text-stroke:.4px currentColor}
.links li{list-style:none;font-size:13px;margin-bottom:11px}
.links li::before{content:"»";margin-right:14px}
.contact div{font-size:13px;margin-bottom:14px;display:flex;gap:10px;align-items:flex-start;line-height:1.4}
.map{width:236px;height:148px;background:linear-gradient(135deg,#e9e7e1,#d7dcd4 60%,#cfd8df);border:4px solid #e8e8e8}
.footer-brand{left:960px;top:92px;text-align:center;width:150px}
.footer-brand .brand-mark{width:40px;height:40px;background:#bdbdbd;margin:0 auto 8px}
.footer-brand .brand-name{color:#dcdcdc;font-size:14px}
.copy{top:3210px;left:0;width:1200px;height:45px;background:var(--navy-dark);color:#e6e6e6;font-size:13px;text-align:center;line-height:45px}
</style>
</head>
<body>

<header class="abs header">
  <div class="abs brand">
    <span class="brand-mark"></span>
    <div class="brand-name">KELTO<br>CONSTRUCTION</div>
  </div>
  <div class="abs topbar">
    <span><span class="ico"><svg width="14" height="14" viewBox="0 0 24 24"><path fill="#fff" d="M6.6 10.8a15 15 0 0 0 6.6 6.6l2.2-2.2c.3-.3.7-.4 1-.2 1.1.4 2.3.6 3.6.6.6 0 1 .4 1 1V20c0 .6-.4 1-1 1A17 17 0 0 1 3 4c0-.6.4-1 1-1h3.5c.6 0 1 .4 1 1 0 1.3.2 2.5.6 3.6.1.3 0 .7-.2 1z"/></svg></span>123-456-7890</span>
    <span><span class="ico"><svg width="14" height="14" viewBox="0 0 24 24"><path fill="#fff" d="M3 5h18v14H3zm2 2v.5l7 4.5 7-4.5V7l-7 4.5z"/></svg></span>info@keltoconstruction.example.com</span>
    <div class="socials">
      <span style="background:#3b5998"></span><span style="background:#2fa9e1"></span><span style="background:#0e76a8"></span><span style="background:#d6382b"></span>
    </div>
  </div>
  <nav class="abs nav">
    <span class="active">HOME</span><span>ABOUT US</span><span>SERVICES</span><span>OUR WORK</span><span>BLOG</span><span>CONTACT US</span>
  </nav>
</header>

<section class="abs hero" role="img" aria-label="Photo of a city skyline with a tall tower across a harbour under a cloudy golden sky">
  <div class="abs arrow" style="left:8px"><svg width="12" height="14"><path d="M10 1 2 7l8 6z" fill="#fff"/></svg></div>
  <div class="abs arrow" style="right:8px"><svg width="12" height="14"><path d="M2 1l8 6-8 6z" fill="#fff"/></svg></div>
  <div class="hero-title"><div class="l1">We Build</div><div class="l2">Your Dreams</div></div>
</section>

<div class="abs band resi">
  <div class="circle"><svg width="56" height="48" viewBox="0 0 56 48"><path d="M28 4 4 24h7v20h13V32h8v12h13V24h7z" fill="#fff"/></svg></div>
  <div><h3>RESIDENTIAL PROJECTS</h3><p>Lorem ipsum dolor sit amet, consectetuer adipiscing elit, sed diam nonummy nibh euismod tincidunt ut laoreet dolore magna aliquam erat...[+]</p></div>
</div>
<div class="abs band comm">
  <div class="circle"><svg width="44" height="52" viewBox="0 0 44 52"><path d="M6 4h32v44H6z" fill="#fff"/><g fill="#8a8b8d"><rect x="12" y="10" width="6" height="6"/><rect x="26" y="10" width="6" height="6"/><rect x="12" y="22" width="6" height="6"/><rect x="26" y="22" width="6" height="6"/><rect x="18" y="36" width="8" height="12"/></g></svg></div>
  <div><h3>COMMERCIAL PROJECTS</h3><p>Lorem ipsum dolor sit amet, consectetuer adipiscing elit, sed diam nonummy nibh euismod tincidunt ut laoreet dolore magna aliquam erat...[+]</p></div>
</div>

<section class="abs about">
  <h2 class="heading">ABOUT KELTO <span>CONSTRUCTION</span></h2>
  <div class="divider"><i></i><b></b><i></i></div>
  <p>Lorem ipsum dolor sit amet, consectetuer adipiscing elit, sed diam nonummy nibh euismod tincidunt ut laoreet dolore magna aliquam erat volutpat. Ut wisi enim ad minim veniam, quis nostrud exerci tation ullamcorper suscipit lobortis nisl ut aliquip ex ea commodo consequat. Duis autem vel eum iriure dolor in hendrerit in vulputate velit esse molestie consequat, vel illum dolore eu feugiat nulla facilisis at vero eros et accumsan et iusto odio dignissim qui blandit praesent luptatum zzril delenit augue duis dolore te feugait nulla facilisi.nibh euismod tincidunt ut laoreet dolore magna aliquam erat volutpat.</p>
  <span class="btn">Read More</span>
</section>

<section class="abs special">
  <h2 class="heading">WE SPECIALIZING <span>IN</span></h2>
  <div class="divider"><i></i><b></b><i></i></div>
  <article class="abs card" style="left:98px">
    <div class="photo" role="img" aria-label="Photo of two builders in hard hats reviewing plans in a bright hall" style="background:linear-gradient(170deg,#efe6d2 0%,#d9c9a8 35%,#b9a483 60%,#8f99a6 85%,#c6c9cc 100%)"></div>
    <div class="badge"><svg width="30" height="30" viewBox="0 0 30 30"><path d="M15 3 3 13h4v14h16V13h4z" fill="#fff"/></svg></div>
    <h4>INTERIOR RENOVATION</h4>
    <p>Lorem ipsum dolor sit amet, consectetur adipiscing elit. Praesent vestibulum velit felis. Maecenas ac faucibus turpis.</p>
    <span class="btn">Read More</span>
  </article>
  <article class="abs card" style="left:442px">
    <div class="photo" role="img" aria-label="Photo of a couple meeting a consultant at a desk" style="background:linear-gradient(100deg,#d9b56a 0%,#b89a72 30%,#5d6f8c 50%,#8b8782 70%,#3d3b3c 100%)"></div>
    <div class="badge"><svg width="28" height="28" viewBox="0 0 28 28"><rect x="4" y="4" width="16" height="20" fill="none" stroke="#fff" stroke-width="2.5"/><path d="M10 18 24 4" stroke="#fff" stroke-width="2.5"/></svg></div>
    <h4>DESIGN &amp; BUILD PACKAGE</h4>
    <p>Lorem ipsum dolor sit amet, consectetur adipiscing elit. Praesent vestibulum velit felis. Maecenas ac faucibus turpis.</p>
    <span class="btn">Read More</span>
  </article>
  <article class="abs card" style="left:786px">
    <div class="photo" role="img" aria-label="Photo of two workers in blue overalls and hard hats painting" style="background:linear-gradient(175deg,#f4f2ec 0%,#e7dfcf 30%,#e0b24a 42%,#c7cbd0 55%,#47689a 75%,#2f4d7a 100%)"></div>
    <div class="badge"><svg width="28" height="28" viewBox="0 0 28 28"><rect x="4" y="4" width="20" height="20" fill="none" stroke="#fff" stroke-width="2.5"/><path d="M4 14h20M14 4v20" stroke="#fff" stroke-width="2.5"/></svg></div>
    <h4>TILING AND PAINTING</h4>
    <p>Lorem ipsum dolor sit amet, consectetur adipiscing elit. Praesent vestibulum velit felis. Maecenas ac faucibus turpis.</p>
    <span class="btn">Read More</span>
  </article>
</section>

<section class="abs work">
  <h2 class="heading">OUR <span>WORK</span></h2>
  <div class="divider"><i></i><b></b><i></i></div>
  <div class="abs tile" style="left:98px;top:135px;width:237px;height:180px;background:linear-gradient(180deg,#e2e0da 0%,#c3c0b8 30%,#b08a5c 55%,#8d6e4a 75%,#7b7a77 100%)" role="img" aria-label="Photo of an interior under construction with timber framing"><div class="cap">LOREM IPSUM</div></div>
  <div class="abs tile" style="left:354px;top:135px;width:236px;height:180px;background:linear-gradient(160deg,#66676a,#48494c 50%,#353638);align-items:center" role="img" aria-label="Photo of a handshake over a desk, dimmed"><div style="color:#fff;font:900 12px Lato,sans-serif;text-align:center">LOREM IPSUM</div></div>
  <div class="abs tile" style="left:610px;top:135px;width:235px;height:380px;background:linear-gradient(180deg,#5a7596 0%,#8196ad 22%,#6a7a89 45%,#3f4b57 70%,#28313a 100%)" role="img" aria-label="Photo of a modern glass office tower at dusk"><div class="cap">LOREM IPSUM</div></div>
  <div class="abs tile" style="left:864px;top:135px;width:236px;height:180px;background:linear-gradient(200deg,#e8b52c 0%,#f0d070 20%,#efede6 45%,#dedcd4 70%,#a9a59c 100%)" role="img" aria-label="Photo of a hard hat and tape measure on building plans"><div class="cap">LOREM IPSUM</div></div>
  <div class="abs tile" style="left:98px;top:335px;width:492px;height:180px;background:linear-gradient(180deg,#8fb4d6 0%,#b9c8d4 22%,#d7d6cf 42%,#8d8a80 58%,#5f8a3c 78%,#3f7a24 100%)" role="img" aria-label="Photo of a two-storey family house with a green lawn and trees"><div class="cap">LOREM IPSUM</div></div>
  <div class="abs tile" style="left:864px;top:335px;width:236px;height:180px;background:linear-gradient(150deg,#8e6440 0%,#c49a64 35%,#d8b37a 55%,#9c6d45 80%,#6e4a30 100%)" role="img" aria-label="Photo of hand tools laid out on a wooden table"><div class="cap">LOREM IPSUM</div></div>
  <span class="btn" style="top:545px">View All</span>
</section>

<section class="abs blog">
  <h2 class="heading">LATEST <span>BLOG POSTS</span></h2>
  <div class="divider"><i></i><b></b><i></i></div>
  <div class="abs feature" role="img" aria-label="Image of a glass office building beside architectural drawings">
    <div class="meta">
      <h5>Lorem ipsum dolor sit amet consectetur.</h5>
      <div class="meta-row"><span>&#9638; 25Mar, 2018</span><span>&#9633; 115 Comments</span><span>&#9825; 210 Likes</span></div>
    </div>
  </div>
  <article class="abs post" style="top:137px">
    <div class="thumb" role="img" aria-label="Photo of engineers in hard hats on a building site" style="background:linear-gradient(170deg,#c8d8e6 0%,#e9e6dc 40%,#8e8f8b 70%,#5d6064 100%)"></div>
    <div><h5>Lorem ipsum dolor sit amet consectetur.</h5>
      <div class="meta-row"><span>&#9638; 21Mar, 2018</span><span>&#9633; 115 Comments</span><span>&#9825; 210 Likes</span></div>
      <p>Lorem ipsum dolor sit amet, consectetuer adipising elit sed diam nonummy nibh euismod tincidunt ut laoreet...[+]</p></div>
  </article>
  <article class="abs post" style="top:242px">
    <div class="thumb" role="img" aria-label="Photo of steel framework against a blue sky" style="background:linear-gradient(180deg,#8fb6dc 0%,#7aa0c4 45%,#6a6058 75%,#3f3a36 100%)"></div>
    <div><h5>Lorem ipsum dolor sit amet consectetur.</h5>
      <div class="meta-row"><span>&#9638; 19Mar, 2018</span><span>&#9633; 115 Comments</span><span>&#9825; 210 Likes</span></div>
      <p>Lorem ipsum dolor sit amet, consectetuer adipising elit sed diam nonummy nibh euismod tincidunt ut laoreet...[+]</p></div>
  </article>
  <article class="abs post" style="top:347px">
    <div class="thumb" role="img" aria-label="Photo of builders working on a timber frame" style="background:linear-gradient(170deg,#d6dbe0 0%,#d9c7a4 40%,#a6845e 70%,#5f5a52 100%)"></div>
    <div><h5>Lorem ipsum dolor sit amet consectetur.</h5>
      <div class="meta-row"><span>&#9638; 05Mar, 2018</span><span>&#9633; 115 Comments</span><span>&#9825; 210 Likes</span></div>
      <p>Lorem ipsum dolor sit amet, consectetuer adipising elit sed diam nonummy nibh euismod tincidunt ut laoreet...[+]</p></div>
  </article>
  <span class="btn" style="top:480px">View All</span>
</section>

<footer class="abs footer">
  <div class="abs" style="left:98px;top:50px">
    <h6>QUICK LINKS</h6>
    <ul class="links"><li>Home</li><li>About Us</li><li>Services</li><li>Our Work</li><li>Blog</li><li>Contact Us</li></ul>
  </div>
  <div class="abs contact" style="left:318px;top:50px">
    <h6>CONTACT DETAILS</h6>
    <div><svg width="14" height="18" viewBox="0 0 14 18"><path d="M7 0a7 7 0 0 0-7 7c0 5 7 11 7 11s7-6 7-11a7 7 0 0 0-7-7zm0 10a3 3 0 1 1 0-6 3 3 0 0 1 0 6z" fill="#fff"/></svg><span><b>KELTO CONSTRUCTION</b><br>123 Lorem ipsum dolor sit amet,<br>consectetuer adipiscing elit.</span></div>
    <div><svg width="14" height="14" viewBox="0 0 24 24"><path fill="#fff" d="M6.6 10.8a15 15 0 0 0 6.6 6.6l2.2-2.2c.3-.3.7-.4 1-.2 1.1.4 2.3.6 3.6.6.6 0 1 .4 1 1V20c0 .6-.4 1-1 1A17 17 0 0 1 3 4c0-.6.4-1 1-1h3.5c.6 0 1 .4 1 1 0 1.3.2 2.5.6 3.6.1.3 0 .7-.2 1z"/></svg>123-456-7890</div>
    <div><svg width="14" height="14" viewBox="0 0 14 14"><rect x="1" y="5" width="12" height="6" fill="#fff"/><rect x="3" y="1" width="8" height="4" fill="none" stroke="#fff"/><rect x="3" y="9" width="8" height="4" fill="#fff"/></svg>123-456-7890</div>
    <div><svg width="14" height="14" viewBox="0 0 24 24"><path fill="#fff" d="M3 5h18v14H3zm2 2v.5l7 4.5 7-4.5V7l-7 4.5z"/></svg>info@keltoconstruction.example.com</div>
  </div>
  <div class="abs" style="left:628px;top:50px">
    <h6>LOCATION MAP</h6>
    <div class="map" role="img" aria-label="Street map showing the office location"></div>
  </div>
  <div class="abs footer-brand">
    <span class="brand-mark" style="display:block"></span>
    <div class="brand-name">KELTO<br>CONSTRUCTION</div>
    <div class="socials" style="justify-content:center;margin-top:14px">
      <span style="background:#3b5998"></span><span style="background:#2fa9e1"></span><span style="background:#0e76a8"></span><span style="background:#d6382b"></span>
    </div>
  </div>
</footer>
<div class="abs copy">Copyright © 2018 KELTO CONSTRUCTION. All Rights Reserved.</div>

</body>
</html>
```